Accounting business needs business card

I have a business card but need something better. I want the colour changed and the design to be better. I have uploaded a picture of my new sign that is grey in colour, i would like to incorporate these colours.

```html
<!DOCTYPE html>
<html lang="en">
<head>
<meta charset="utf-8">
<title>Level Tax – Business Card</title>
<link rel="stylesheet" href="https://fonts.googleapis.com/css2?family=Poppins:wght@400;500;700&display=swap">
<style>
  :root {
    --bg: #2b2f33;
    --card-white: #ffffff;
    --card-grey: #dedede;
    --teal: #25b99a;
    --ink: #1f1f1f;
    --text-grey: #3c3c3c;
    --stripe-grey: #c9c9c9;
    --stripe-light: #d9d9d9;
    --stripe-dark: #2a2a2a;
    --badge-fill: #e4e4e4;
    --badge-edge: #cfcfcf;
    --social-grey: #c4c4c4;
  }
  * { margin: 0; padding: 0; box-sizing: border-box; }
  html, body { width: 1200px; height: 985px; overflow: hidden; }
  body {
    background: var(--bg);
    font-family: "Poppins", sans-serif;
    position: relative;
  }
  .card {
    position: absolute;
    top: 337px;
    width: 540px;
    height: 310px;
    border-radius: 18px;
    overflow: hidden;
    box-shadow: 0 14px 30px rgba(0,0,0,0.45);
  }
  .card-back { left: 40px; background: var(--card-grey); }
  .card-front { left: 620px; background: var(--card-white); }

  /* back */
  .social-row { position: absolute; top: 22px; left: 24px; display: flex; gap: 8px; }
  .social-dot { width: 20px; height: 20px; border-radius: 50%; background: var(--social-grey); }
  .brand {
    position: absolute;
    display: flex;
    align-items: center;
    gap: 18px;
  }
  .brand-mark {
    border: 3px solid var(--ink);
    border-radius: 50%;
    flex: none;
  }
  .brand-name {
    font-weight: 500;
    color: var(--ink);
    letter-spacing: 0.42em;
    white-space: nowrap;
  }
  .card-back .brand { left: 50%; top: 50%; transform: translate(-50%, -50%); }
  .card-back .brand-mark { width: 78px; height: 78px; }
  .card-back .brand-name { font-size: 30px; }

  /* front */
  .wave { position: absolute; left: 0; top: 0; width: 540px; height: 310px; }
  .contact-block { position: absolute; left: 30px; top: 24px; }
  .person-name { font-size: 22px; font-weight: 700; color: var(--teal); line-height: 1.1; }
  .credentials, .job-title { font-size: 11.5px; color: var(--text-grey); line-height: 1.55; }
  .credentials { margin-top: 4px; }
  .contact-list { list-style: none; margin-top: 10px; }
  .contact-list li {
    display: flex; align-items: center; gap: 7px;
    font-size: 11.5px; color: var(--text-grey); line-height: 1.7;
  }
  .contact-list svg { width: 10px; height: 10px; fill: var(--teal); flex: none; }
  .badges { position: absolute; left: 30px; top: 160px; display: flex; align-items: flex-start; gap: 12px; }
  .badge {
    width: 44px; height: 34px; border-radius: 4px;
    background: var(--badge-fill); border: 1px solid var(--badge-edge);
  }
  .badge-wide { width: 86px; }
  .badge-wrap { display: flex; flex-direction: column; align-items: center; }
  .agent-number { font-size: 7px; color: var(--text-grey); margin-top: 3px; line-height: 1.2; text-align: center; }
  .card-front .brand { right: 34px; top: 140px; flex-direction: column; align-items: flex-end; gap: 12px; }
  .card-front .brand-mark { width: 60px; height: 60px; }
  .card-front .brand-name { font-size: 24px; }
</style>
</head>
<body>

<section class="card card-back" aria-label="Card back">
  <div class="social-row">
    <span class="social-dot"></span>
    <span class="social-dot"></span>
    <span class="social-dot"></span>
  </div>
  <div class="brand">
    <span class="brand-mark"></span>
    <span class="brand-name">LEVEL TAX</span>
  </div>
</section>

<section class="card card-front" aria-label="Card front">
  <svg class="wave" viewBox="0 0 540 310" aria-hidden="true">
    <path d="M0,212 C150,226 268,262 330,310 L0,310 Z" fill="var(--stripe-grey)"/>
    <path d="M0,221 C145,234 258,268 316,310 L0,310 Z" fill="#ffffff"/>
    <path d="M0,227 C140,240 250,272 304,310 L0,310 Z" fill="var(--stripe-dark)"/>
    <path d="M0,234 C135,247 242,276 294,310 L0,310 Z" fill="var(--stripe-light)"/>
    <path d="M0,241 C125,254 230,280 280,310 L0,310 Z" fill="var(--teal)"/>
  </svg>

  <div class="contact-block">
    <h1 class="person-name">Dean Whitford</h1>
    <p class="credentials">CAP, MTAX, BCOM (Acc &amp; Fin)</p>
    <p class="job-title">Taxation and Business Accountant</p>
    <ul class="contact-list">
      <li><svg viewBox="0 0 10 10"><path d="M2,0 L4,2.5 L3,3.6 C3.8,5 5,6.2 6.4,7 L7.5,6 L10,8 L8.5,10 C4,9.5 0.5,6 0,1.5 Z"/></svg>0412 555 308</li>
      <li><svg viewBox="0 0 10 10"><path d="M0,2 H10 V8.5 H0 Z"/></svg>dean@leveltax.com.au</li>
      <li><svg viewBox="0 0 10 10"><circle cx="5" cy="5" r="5"/></svg>www.leveltax.com.au</li>
    </ul>
  </div>

  <div class="badges" aria-label="Membership badges">
    <div class="badge badge-wide"></div>
    <div class="badge"></div>
    <div class="badge-wrap">
      <div class="badge"></div>
      <p class="agent-number">Tax agent<br>27150392</p>
    </div>
  </div>

  <div class="brand">
    <span class="brand-mark"></span>
    <span class="brand-name">LEVEL TAX</span>
  </div>
</section>

</body>
</html>
```